ORLA - Óptica Médica - web design and concept

Website concept - Create and develop our website design and structure. ORLA is an optical store chain, and we are looking to establish our web and digital concept. In attachment there are several pictures about our stores and our logo.

The website structure should be user friendly. Colors should be light and the design as simple and minimalist as possible. There are different variations of the logothat can be used, check the file.

The website will include optical collections and sun collections as an online store. Also, a medical menu should be considered in order for clients to schedule optometry appointments. There should also be a menu for client assistance where the clients can read about glass maintenance in our workshop.
Updates

Low design quality

Number of Pages Required

5+ page

Font styles to use
Serif
Sans Serif

Requirements
Must have
• Must be user-friendly and minimalist.
• Please USE PICTURES FROM THE BRANDS we sell: MERUN, BOSKA, PNW, KOLE, BAMPE
Nice to have
• Nice to inspire: ZEK glasses (see website https://ch.shopzek.com/en/)
• Nice to inspire: https://merun-eyewear.com/
• Nice to ispire: https://www.pnwglobe.com/en/
Should not have
• Hysteric colors and shapes

```html
<!DOCTYPE html>
<html lang="en">
<head>
<meta charset="utf-8">
<title>ORLA Óptica Médica</title>
<link rel="stylesheet" href="https://fonts.googleapis.com/css2?family=Lato:wght@300;400;700;900&family=Cinzel:wght@400;700&display=swap">
<style>
:root{
  --gold:#c9963f;
  --gold-dark:#b5832f;
  --ink:#222;
  --text:#666;
  --night:#1b1b1b;
  --footer:#262626;
  --soft:#f3f3f3;
  --white:#fff;
}
*{box-sizing:border-box;margin:0;padding:0}
html,body{width:1200px;height:3636px;overflow:hidden}
body{font-family:'Lato',sans-serif;color:var(--ink);background:var(--white);position:relative}
.abs{position:absolute}
/* header */
.site-header{position:absolute;left:0;top:0;width:1200px;height:120px;background:var(--night);z-index:3}
.brand{position:absolute;left:96px;top:30px;text-align:center;color:var(--gold);font-family:'Cinzel',serif}
.brand .name{font-size:34px;letter-spacing:6px}
.brand .sub{font-family:'Lato',sans-serif;font-size:9px;letter-spacing:3px;margin-top:2px}
.nav a{position:absolute;top:50px;font-size:14px;color:var(--white);text-decoration:none;letter-spacing:.5px}
.nav a.active{color:var(--gold)}
.header-tools{position:absolute;left:1034px;top:48px;color:var(--gold);font-size:13px;display:flex;gap:18px;align-items:center}
/* hero */
.hero{position:absolute;left:0;top:120px;width:1200px;height:620px;background:linear-gradient(180deg,#3a3a3c 0%,#5b5a58 45%,#6b5238 100%);clip-path:polygon(0 0,100% 0,100% 540px,0 610px)}
.hero-title{position:absolute;left:0;width:1200px;top:290px;text-align:center;color:var(--white);font-size:118px;font-weight:900;letter-spacing:4px;z-index:2}
.hero-text{position:absolute;left:250px;width:700px;top:408px;text-align:center;color:var(--white);font-size:21px;line-height:29px;z-index:2}
.slider-arrow{position:absolute;top:364px;width:46px;height:46px;border-radius:50%;background:rgba(255,255,255,.18);z-index:2}
/* welcome */
.welcome{position:absolute;left:0;top:660px;width:1200px;height:452px;background:var(--gold);z-index:0}
.section-title{position:absolute;left:0;width:1200px;text-align:center;font-size:36px;font-weight:700;text-transform:uppercase}
.section-title::after{content:"";display:block;width:76px;height:3px;background:var(--gold);margin:14px auto 0}
.welcome .section-title{color:var(--white);top:128px}
.welcome .section-title::after{background:var(--white);width:60px}
.welcome-text{position:absolute;left:160px;width:880px;top:196px;text-align:center;color:var(--white);font-size:19px;line-height:28px}
.btn-outline{position:absolute;left:502px;top:317px;width:196px;height:49px;border:3px solid var(--white);color:var(--white);font-size:19px;font-weight:700;text-align:center;line-height:43px}
/* guarantees */
.guarantees{position:absolute;left:0;top:1112px;width:1200px;height:560px;background:var(--white)}
.guarantees .section-title{top:76px}
.g-item{position:absolute;top:194px;width:180px;margin-left:-90px;text-align:center}
.g-icon{width:108px;height:108px;border-radius:50%;background:#f6f6f6;margin:0 auto;display:flex;align-items:center;justify-content:center}
.g-item h3{font-size:17px;font-weight:700;margin-top:24px;line-height:22px;min-height:44px;display:flex;align-items:center;justify-content:center}
.g-item p{font-size:14px;line-height:20px;color:var(--text);margin-top:6px}
/* products */
.products{position:absolute;left:0;top:1672px;width:1200px;height:614px;background:linear-gradient(180deg,var(--gold-dark),var(--gold))}
.products .section-title{color:var(--white);top:60px}
.products .section-title::after{background:var(--white)}
.mini-arrow{position:absolute;top:115px;width:24px;height:24px;border:1px solid var(--white)}
.p-card{position:absolute;top:163px;width:223px;height:359px;background:var(--white);box-shadow:0 4px 10px rgba(0,0,0,.2)}
.p-photo{width:223px;height:182px}
.p-card h3{font-size:16px;font-weight:700;margin:20px 0 0 18px;text-transform:uppercase}
.p-card p{font-size:11px;line-height:16px;color:var(--text);margin:14px 16px 0 18px;height:50px}
.learn{display:block;margin:12px 0 0 18px;font-size:11px;font-weight:700;color:var(--gold)}
/* blog */
.blog{position:absolute;left:0;top:2286px;width:1200px;height:606px;background:var(--soft)}
.blog .section-title{top:70px}
.b-card{position:absolute;top:179px;width:300px;height:230px;border:5px solid var(--white);box-shadow:0 3px 8px rgba(0,0,0,.18);color:var(--white)}
.b-card h3{position:absolute;left:14px;bottom:46px;width:260px;font-size:18px;font-weight:900;line-height:21px;text-transform:uppercase}
.b-card .date{position:absolute;left:14px;bottom:26px;font-size:11px}
.b-card .read{position:absolute;left:14px;bottom:-2px;font-size:11px;font-weight:700}
.b-card.featured h3{bottom:108px}
.b-card.featured .date{bottom:88px}
.b-card.featured .read{bottom:58px}
.btn-solid{position:absolute;left:526px;top:485px;width:148px;height:43px;background:var(--gold);color:var(--white);font-weight:700;font-size:18px;text-align:center;line-height:43px;box-shadow:0 2px 4px rgba(0,0,0,.2)}
/* brands */
.brands{position:absolute;left:0;top:2892px;width:1200px;height:368px;background:var(--white)}
.brands .section-title{top:66px}
.brand-box{position:absolute;top:172px;width:178px;height:116px;border:1px solid #ddd;box-shadow:0 1px 4px rgba(0,0,0,.1);display:flex;align-items:center;justify-content:center;font-size:17px;font-weight:900;letter-spacing:1px;text-transform:uppercase}
/* footer */
.site-footer{position:absolute;left:0;top:3260px;width:1200px;height:376px;background:var(--footer);color:#ccc}
.f-brand{position:absolute;left:98px;top:74px;text-align:center;color:var(--gold);font-family:'Cinzel',serif}
.f-brand .mark{width:70px;height:70px;border:2px solid var(--gold);border-radius:50%;margin:0 auto 14px}
.f-brand .name{font-size:44px;letter-spacing:8px}
.f-brand .sub{font-family:'Lato',sans-serif;font-size:10px;letter-spacing:4px}
.f-col{position:absolute;top:78px;font-size:12px;line-height:32px}
.f-col h4{font-size:17px;font-weight:700;color:var(--white);margin-bottom:10px;line-height:22px}
.f-col ul{list-style:none}
.contact-line{display:flex;gap:8px;align-items:flex-start;line-height:18px;margin-bottom:12px}
.socials{display:flex;gap:8px;margin-top:10px}
.socials span{width:15px;height:15px;border-radius:50%;background:#ccc}
.footer-rule{position:absolute;left:97px;top:303px;width:1006px;height:1px;background:#3a3a3a}
.copyright{position:absolute;left:0;width:1200px;top:330px;text-align:center;font-size:11px}
</style>
</head>
<body>

<header class="site-header">
  <div class="brand"><div class="name">ORLA</div><div class="sub">ÓPTICA MÉDICA</div></div>
  <nav class="nav">
    <a class="active" style="left:318px">HOME</a>
    <a style="left:413px">ABOUT US</a>
    <a style="left:533px">PRODUCTS</a>
    <a style="left:655px">BLOG</a>
    <a style="left:745px">STORE</a>
    <a style="left:841px">CONTACT</a>
  </nav>
  <div class="header-tools">
    <svg width="14" height="14" viewBox="0 0 14 14"><circle cx="6" cy="6" r="4.5" fill="none" stroke="#c9963f" stroke-width="1.6"/><path d="M9.5 9.5 13 13" stroke="#c9963f" stroke-width="1.6"/></svg>
    <span>&#9635; (0)</span>
  </div>
</header>

<section class="hero" role="img" aria-label="Interior of an optical store with wooden counter, lit display walls and a black chandelier"></section>
<h1 class="hero-title">ORLA OPTICA</h1>
<p class="hero-text">We are an optical store chain. We are focused on bringing the best optical assistance and eyewear brands to our costumers.</p>
<div class="slider-arrow" style="left:18px"></div>
<div class="slider-arrow" style="left:1136px"></div>

<section class="welcome">
  <h2 class="section-title">Welcome to Orla Optics</h2>
  <p class="welcome-text">ORLA OPTICA opens its doors with a clear purpose: to take care of you. Our priority is your visual health, and for this reason we have the best professionals and the most competitive products to serve your needs.</p>
  <div class="btn-outline">CONTACT US</div>
</section>

<section class="guarantees">
  <h2 class="section-title">Our Guarantees</h2>
  <div class="g-item" style="left:182px">
    <div class="g-icon"><svg width="40" height="40" viewBox="0 0 40 40"><path d="M20 34 6 20a8 8 0 0 1 14-10 8 8 0 0 1 14 10z" fill="#c9963f"/></svg></div>
    <h3>Orla Childhood Guarantee</h3>
    <p>50% discount on new glasses, if your child's graduation has changed before six months.</p>
  </div>
  <div class="g-item" style="left:388px">
    <div class="g-icon"><svg width="44" height="34" viewBox="0 0 44 34"><rect x="2" y="6" width="26" height="20" fill="#c9963f"/><path d="M28 12h8l6 7v7H28z" fill="#c9963f"/><circle cx="10" cy="28" r="4" fill="#fff" stroke="#c9963f" stroke-width="2"/><circle cx="34" cy="28" r="4" fill="#fff" stroke="#c9963f" stroke-width="2"/><path d="M15 11v10M10 16h10" stroke="#fff" stroke-width="3"/></svg></div>
    <h3>Orla Accident Warranty</h3>
    <p>Did you get off your glasses when you got out of the car? Did your little boy play with his sunglasses?</p>
  </div>
  <div class="g-item" style="left:599px">
    <div class="g-icon"><svg width="36" height="40" viewBox="0 0 36 40"><rect x="5" y="17" width="26" height="20" rx="2" fill="#c9963f"/><path d="M10 17v-5a8 8 0 0 1 16 0v5" fill="none" stroke="#c9963f" stroke-width="4"/></svg></div>
    <h3>Orla Security</h3>
    <p>If you have suffered a robbery or robbery in your home, you will opt for the replacement of the same product at half price.</p>
  </div>
  <div class="g-item" style="left:807px">
    <div class="g-icon"><svg width="46" height="30" viewBox="0 0 46 30"><path d="M2 15Q23-8 44 15 23 38 2 15z" fill="#c9963f"/><circle cx="23" cy="15" r="7" fill="#fff"/><circle cx="23" cy="15" r="3.5" fill="#c9963f"/></svg></div>
    <h3>Orla Vision</h3>
    <p>If you suffer from a diagnosed visual pathology and during the first two years your graduation changes, we replenish your crystals to 50%.</p>
  </div>
  <div class="g-item" style="left:1018px">
    <div class="g-icon"><svg width="34" height="40" viewBox="0 0 34 40"><path d="M17 2 32 8v12c0 9-7 15-15 18C9 35 2 29 2 20V8z" fill="none" stroke="#c9963f" stroke-width="3"/><path d="m10 20 5 5 9-10" fill="none" stroke="#c9963f" stroke-width="3"/></svg></div>
    <h3>Manufacturer's Warranty</h3>
    <p>All our products have the legal guarantee of the manufacturer. They will be free parts if in the first 2 years they suffer some deterioration due to factory default.</p>
  </div>
</section>

<section class="products">
  <h2 class="section-title">Our Products</h2>
  <div class="mini-arrow" style="left:1043px"></div>
  <div class="mini-arrow" style="left:1076px"></div>
  <article class="p-card" style="left:102px">
    <div class="p-photo" role="img" aria-label="Woman wearing black graduated frames" style="background:linear-gradient(135deg,#e8ded6,#6b4a3a)"></div>
    <h3>Graduated Frame</h3>
    <p>We have a selection of frames from the best brands; Lena Marot, Alvena, Valdri, Ferro Lind, Mirel...</p>
    <span class="learn">LEARN MORE ⟶</span>
  </article>
  <article class="p-card" style="left:359px">
    <div class="p-photo" role="img" aria-label="Child wearing red glasses" style="background:linear-gradient(135deg,#f3e9dc,#d9b48a)"></div>
    <h3>Special Children</h3>
    <p>Our professionals will right type of lens for your child, guaranteeing the best treatment for your visual problem.</p>
    <span class="learn">LEARN MORE ⟶</span>
  </article>
  <article class="p-card" style="left:616px">
    <div class="p-photo" role="img" aria-label="Two clear ophthalmic lenses" style="background:linear-gradient(135deg,#f4f4f4,#b9b9b9)"></div>
    <h3>Ophthalmic Lenses</h3>
    <p>We guarantee our clients a personalized attention, suitable type of lens for their pathology of life and daily routine...</p>
    <span class="learn">LEARN MORE ⟶</span>
  </article>
  <article class="p-card" style="left:873px">
    <div class="p-photo" role="img" aria-label="Contact lens resting on a fingertip" style="background:linear-gradient(180deg,#6fb6e8,#d9c3b0)"></div>
    <h3>Contact Lenses</h3>
    <p>As experts in the adaptation of contact lenses, our professionals advice on the choice of contact lenses to your needs.</p>
    <span class="learn">LEARN MORE ⟶</span>
  </article>
</section>

<section class="blog">
  <h2 class="section-title">Our Blog</h2>
  <article class="b-card" style="left:102px;background:linear-gradient(135deg,#4a8fb0,#c7563b 55%,#6a3d7a)" role="img" aria-label="Video still of an optician with colourful title graphics">
    <h3>What color are the bananas?</h3><span class="date">APRIL 14, 2015</span>
  </article>
  <article class="b-card featured" style="left:451px;background:linear-gradient(135deg,#2e2e2e,#4a4a4a)" role="img" aria-label="Video still of an optician, darkened for the featured post">
    <h3>Should you put sunglasses on your children?</h3><span class="date">JANUARY 20, 2015</span><span class="read">READ MORE &#9679;</span>
  </article>
  <article class="b-card" style="left:795px;background:linear-gradient(135deg,#b9c8d2,#7a6a66 60%,#c44a3a)" role="img" aria-label="Video still of an optician with a title about colour blindness">
    <h3>An approach to color blindness</h3><span class="date">APRIL 14, 2015</span>
  </article>
  <div class="btn-solid">VIEW MORE</div>
</section>

<section class="brands">
  <h2 class="section-title">Our Brands</h2>
  <div class="brand-box" style="left:114px">Norvik</div>
  <div class="brand-box" style="left:318px">Lena Marot</div>
  <div class="brand-box" style="left:519px">Valdri</div>
  <div class="brand-box" style="left:713px">Alvena</div>
  <div class="brand-box" style="left:904px">Tiberra</div>
</section>

<footer class="site-footer">
  <div class="f-brand"><div class="mark"></div><div class="name">ORLA</div><div class="sub">ÓPTICA MÉDICA</div></div>
  <div class="f-col" style="left:390px">
    <h4>Quick Links</h4>
    <ul><li>Home</li><li>About us</li><li>Products</li><li>Blog</li><li>Store</li></ul>
  </div>
  <div class="f-col" style="left:604px">
    <h4>Hours</h4>
    <ul><li>Monday - Friday: 10:00 - 14:00 and 17:00 - 20:30</li><li>Saturday: 10:00 - 14:00</li></ul>
  </div>
  <div class="f-col" style="left:962px;width:150px">
    <h4>Contact Us</h4>
    <div class="contact-line"><svg width="10" height="14" viewBox="0 0 10 14"><path d="M5 14S0 8 0 5a5 5 0 0 1 10 0c0 3-5 9-5 9z" fill="#ccc"/><circle cx="5" cy="5" r="2" fill="#262626"/></svg><span>Calle Olmeda, 15, Valverde</span></div>
    <div class="contact-line"><svg width="12" height="12" viewBox="0 0 12 12"><path d="M2 0 4.5 3 3 4.5a8 8 0 0 0 4.5 4.5L9 7.5l3 2.5-2 2C5 12 0 7 0 2z" fill="#ccc"/></svg><span>983 00 47 12</span></div>
    <div class="contact-line"><svg width="12" height="10" viewBox="0 0 12 10"><rect width="12" height="10" fill="#ccc"/><path d="m0 0 6 5 6-5" fill="none" stroke="#262626"/></svg><span>hola@orlaoptica.es</span></div>
    <div class="socials"><span></span><span></span><span></span><span></span><span></span></div>
  </div>
  <div class="footer-rule"></div>
  <p class="copyright">© 2018 ORLA OPTICA . All right reserved . Term of Use</p>
</footer>

</body>
</html>
```